Website design and coding for new consultancy company

I need to have a full website designed for a new consultancy business I'm trying to establish. It's called BrightPath consult. I need an English version to begin with, and then there should be a Danish version as well, but I'll translate that myself. Just be aware that I need two language versions. The consultancy field that I'm targeting is Leadership - and specialist development. I offer to facilitate corporate academies for global companies as well as specific workshops within leadership- or team development, strategy sessions, personal coaching and facilitation of D&I (Diversity and inclusion) workshops. BTW my logo is not in high resolution - I need that as well.

Target Market(s)

Larger companies that has a need for developing their inhouse leadership capabilities or that wants to develop their specialists to take on more responsibility.

Industry/Entity Type

Consultancy business

Coding

Coded - Design and coding required

Number of Pages Required

5+ page

Requirements
Must have
• Introduction site with a catch phrase. Book a meeting. Services that's beeing offered. Blog site with white papers etc. Language toggle (Danish/English). Cases/testimonials. About site. Contact site.

```html
<!DOCTYPE html>
<html lang="en">
<head>
<meta charset="utf-8">
<title>BrightPath consult – Lead with confidence</title>
<link rel="stylesheet" href="https://fonts.googleapis.com/css2?family=Bebas+Neue&family=Lato:wght@400;700&display=swap">
<style>
:root{
  --blue:#2a7fcf;
  --blue-dark:#1f6db6;
  --ink:#111;
  --text:#333;
  --muted:#666;
  --pale:#dde8f3;
  --star:#f5a623;
  --white:#fff;
}
*{box-sizing:border-box;margin:0;padding:0}
html,body{width:1200px;height:3957px;overflow:hidden}
body{position:relative;font-family:'Lato',sans-serif;color:var(--text);background:var(--white)}
.abs{position:absolute}
.display{font-family:'Bebas Neue',sans-serif;font-weight:400;letter-spacing:1px}
.eyebrow{font-family:'Bebas Neue',sans-serif;color:var(--blue);font-size:15px;letter-spacing:1px;text-align:center}
.section-title{font-family:'Bebas Neue',sans-serif;font-size:56px;color:var(--ink);text-align:center;letter-spacing:2px;line-height:1}
.btn{background:var(--blue);color:var(--white);font-weight:700;font-size:15px;display:flex;align-items:center;justify-content:center;border-radius:3px}

/* header */
.topline{top:0;left:0;width:1200px;height:4px;background:var(--blue)}
.header{top:4px;left:0;width:1200px;height:76px;background:var(--white)}
.brand{left:110px;top:20px;display:flex;align-items:center;gap:12px}
.brand .mark{width:32px;height:32px;border-radius:50%;background:var(--blue)}
.brand .name{font-family:'Lato',sans-serif;font-weight:700;font-size:30px;color:var(--ink);line-height:1}
.nav{left:422px;top:26px;display:flex;gap:40px;font-size:16px;color:var(--ink)}
.nav .active{color:var(--blue);position:relative}
.nav .active::after{content:"";position:absolute;left:0;right:0;top:42px;height:4px;background:var(--blue)}
.lang{left:863px;top:30px;font-size:14px;color:var(--ink);display:flex;align-items:center;gap:4px}
.contact-btn{left:965px;top:20px;width:122px;height:44px}

/* hero */
.hero-photo{top:80px;left:0;width:1200px;height:680px;background:linear-gradient(180deg,#e9eef2 0%,#c9d1d8 45%,#6b5a4e 100%);clip-path:polygon(0 0,100% 0,100% 82%,50% 97%,0 82%)}
.hero-band{top:560px;left:0}
.hero-title{left:110px;top:128px;font-size:80px;line-height:80px;letter-spacing:3px}
.hero-title .l1{color:var(--blue)}
.hero-title .l2{color:var(--ink)}
.hero-btn{left:115px;top:305px;width:165px;height:44px}

/* services */
.card{top:937px;width:316px;height:401px;background:var(--white);box-shadow:0 4px 16px rgba(0,0,0,.15)}
.card .ph{height:308px}
.card .label{height:93px;display:flex;align-items:center;justify-content:center;text-align:center;font-size:21px;color:var(--ink);line-height:1.6}
.card.featured .label{background:var(--blue);color:var(--white);font-weight:700}
.card .icon{position:absolute;left:118px;top:250px;width:72px;height:72px;border-radius:50%;background:var(--blue);border:4px solid var(--white);display:flex;align-items:center;justify-content:center}

/* journey */
.journey{top:1426px;left:0;width:1200px;height:458px;background:var(--pale)}
.journey-h{left:110px;top:1478px;font-size:56px;color:var(--ink);letter-spacing:2px;line-height:1}
.journey-text{left:110px;top:1572px;width:455px;font-size:14px;line-height:32.5px;color:var(--text)}
.journey-btn{left:113px;top:1760px;width:114px;height:44px}
.portrait{left:640px;top:1481px;width:451px;height:354px;border:3px solid var(--blue);background:radial-gradient(circle at 50% 40%,#e8d4c6 0%,#d7dde3 40%,#eef1f4 75%)}

/* why */
.tri{left:455px;top:2130px}
.benefit{width:320px}
.benefit h4{font-size:17px;font-weight:400;color:var(--ink);margin-bottom:6px}
.benefit p{font-size:14px;color:var(--muted);line-height:23px}
.benefit.left{text-align:right}
.b-icon{width:60px;height:60px;border-radius:50%;background:var(--blue);display:flex;align-items:center;justify-content:center}

/* testimonials */
.testimonials{top:2463px;left:0;width:1200px;height:452px;background:var(--pale)}
.avatar{width:74px;height:74px;border-radius:50%;background:radial-gradient(circle at 50% 40%,#e5d5c8,#cfd6dc)}
.t-role{font-size:22px;color:var(--ink)}
.stars{color:var(--star);font-size:23px;letter-spacing:1px}
.t-quote{width:446px;font-size:17px;line-height:30px;color:var(--text);text-align:justify}
.divider{left:597px;top:2645px;height:180px;border-left:2px dashed #bcc7d3}
.dots{left:580px;top:2850px;display:flex;gap:4px}
.dots span{width:7px;height:7px;border-radius:50%;border:1px solid #9aa;background:transparent}
.dots span.on{background:var(--blue);border-color:var(--blue)}

/* news */
.post{top:3103px;width:314px;height:377px;background:var(--white);box-shadow:0 3px 14px rgba(0,0,0,.14)}
.post .ph{height:211px}
.post .body{padding:12px 14px}
.post .cat{font-size:14px;font-weight:700;color:var(--blue);margin-bottom:6px}
.post h3{font-size:18px;font-weight:400;color:var(--ink);line-height:26px;height:60px}
.post .meta{margin-top:10px;font-size:13px;color:var(--muted);display:flex;gap:30px}

/* footer */
.footer-bg{top:3555px;left:0}
.f-brand{left:0;top:3655px;width:1200px;display:flex;align-items:center;justify-content:center;gap:16px}
.f-brand .mark{width:50px;height:50px;border-radius:50%;background:var(--white)}
.f-brand .name{font-family:'Lato',sans-serif;font-weight:700;font-size:50px;color:var(--white);line-height:1}
.socials{left:536px;top:3752px;display:flex;gap:8px}
.socials span{width:28px;height:28px;border-radius:50%;background:var(--white)}
.f-links{left:0;top:3810px;width:1200px;display:flex;justify-content:center;gap:18px;font-size:17px;color:var(--white)}
.f-contact{top:3862px;display:flex;align-items:center;gap:10px;color:var(--white);font-size:16px}
.f-line{left:110px;top:3918px;width:980px;height:1px;background:rgba(255,255,255,.7)}
.copyright{left:0;top:3928px;width:1200px;text-align:center;color:var(--white);font-size:14px}
</style>
</head>
<body>

<div class="abs topline"></div>
<header class="abs header">
  <div class="abs brand"><span class="mark"></span><span class="name">BrightPath</span></div>
  <nav class="abs nav">
    <span class="active">Home</span><span>About Us</span><span>Services</span><span>Testimonials</span>
  </nav>
  <div class="abs lang">
    <svg width="15" height="15" viewBox="0 0 16 16" fill="none" stroke="#111" stroke-width="1.2"><circle cx="8" cy="8" r="6.5"/><ellipse cx="8" cy="8" rx="3" ry="6.5"/><path d="M1.5 8h13"/></svg>
    ENG
    <svg width="14" height="10" viewBox="0 0 14 10" fill="none" stroke="#111" stroke-width="1.8"><path d="M2 2l5 5 5-5"/></svg>
  </div>
  <div class="abs btn contact-btn">CONTACT US</div>
</header>

<section>
  <div class="abs hero-photo" role="img" aria-label="Speaker presenting to a seated audience in a bright conference room"></div>
  <svg class="abs hero-band" width="1200" height="200" viewBox="0 0 1200 200">
    <path d="M0 77 L600 180 L1200 77 L1200 60 L600 145 L0 60 Z" fill="#2a7fcf"/>
  </svg>
  <h1 class="abs display hero-title"><span class="l1">LEAD WITH CONFIDENCE</span><br><span class="l2">GROW WITH PURPOSE</span></h1>
  <div class="abs btn hero-btn">Book a Consultation</div>
</section>

<section>
  <h2 class="abs section-title" style="left:0;top:822px;width:1200px">WHAT WE DO</h2>
  <div class="abs eyebrow" style="left:0;top:882px;width:1196px">OUR SERVICES</div>

  <div class="abs card" style="left:110px">
    <div class="ph" role="img" aria-label="Leadership team meeting around a table in a dark office" style="background:linear-gradient(160deg,#3b4450,#6d625b)"></div>
    <div class="label">Leadership Development<br>&amp; Coaching</div>
  </div>
  <div class="abs card featured" style="left:441px">
    <div class="ph" role="img" aria-label="Colleagues collaborating around a laptop in a workshop" style="background:linear-gradient(160deg,#c9b79f,#7a6a5a)"></div>
    <div class="label" style="padding-top:10px">Team &amp; Strategy Workshops</div>
    <div class="icon">
      <svg width="38" height="38" viewBox="0 0 40 40" fill="#fff"><circle cx="20" cy="9" r="4"/><circle cx="8" cy="24" r="3.5"/><circle cx="20" cy="24" r="3.5"/><circle cx="32" cy="24" r="3.5"/><path d="M3 36c0-4 2.5-6 5-6s5 2 5 6zM15 36c0-4 2.5-6 5-6s5 2 5 6zM27 36c0-4 2.5-6 5-6s5 2 5 6z"/></svg>
    </div>
  </div>
  <div class="abs card" style="left:771px">
    <div class="ph" role="img" aria-label="Business professionals in a corporate academy session" style="background:linear-gradient(160deg,#d8dde2,#5c5a58)"></div>
    <div class="label">Corporate Academies</div>
  </div>
</section>

<section>
  <div class="abs journey"></div>
  <h2 class="abs display journey-h">MY JOURNEY</h2>
  <div class="abs eyebrow" style="left:110px;top:1540px;text-align:left">ABOUT ME</div>
  <p class="abs journey-text">I founded BrightPath Consult with a simple belief: great leadership is not about titles, but about people. With years of experience facilitating leadership programs, strategy sessions, and diversity workshops for global organizations, I have seen first-hand how the right guidance can transform both individuals and teams.</p>
  <div class="abs btn journey-btn">READ MORE</div>
  <div class="abs portrait" role="img" aria-label="Portrait of the founder in a dark blazer"></div>
</section>

<section>
  <h2 class="abs section-title" style="left:0;top:1970px;width:1200px">WHY CHOOSE US</h2>
  <div class="abs eyebrow" style="left:0;top:2035px;width:1200px">OUR BENEFITS</div>

  <svg class="abs tri" width="290" height="250" viewBox="0 0 290 250">
    <defs><clipPath id="tc"><path d="M145 10 L280 240 L10 240 Z"/></clipPath></defs>
    <path d="M145 2 L288 246 L2 246 Z" fill="#2a7fcf"/>
    <rect x="0" y="0" width="290" height="250" fill="#d9e3ec" clip-path="url(#tc)" role="img" aria-label="Smiling consultant gesturing"/>
  </svg>

  <div class="abs benefit left" style="left:132px;top:2122px"><h4>Personalized Approach</h4><p>We don't believe in one-size-fits-all solutions</p></div>
  <div class="abs b-icon" style="left:465px;top:2114px"><svg width="26" height="26" viewBox="0 0 24 24" fill="#fff"><circle cx="12" cy="9" r="4"/><path d="M4 21c0-5 4-7 8-7s8 2 8 7z"/></svg></div>

  <div class="abs benefit left" style="left:92px;top:2210px"><h4>Global Perspective</h4><p>With experience facilitating leadership<br>and team development</p></div>
  <div class="abs b-icon" style="left:422px;top:2208px"><svg width="28" height="28" viewBox="0 0 24 24" fill="none" stroke="#fff" stroke-width="1.8"><circle cx="12" cy="12" r="9"/><ellipse cx="12" cy="12" rx="4" ry="9"/><path d="M3 12h18"/></svg></div>

  <div class="abs benefit left" style="left:35px;top:2312px"><h4>Proven Impact</h4><p>Our work delivers measurable<br>results — stronger leaders</p></div>
  <div class="abs b-icon" style="left:372px;top:2310px"><svg width="28" height="28" viewBox="0 0 24 24" fill="none" stroke="#fff" stroke-width="2"><circle cx="12" cy="12" r="9"/><circle cx="12" cy="12" r="5"/><circle cx="12" cy="12" r="1.5" fill="#fff"/></svg></div>

  <div class="abs b-icon" style="left:648px;top:2112px"><svg width="26" height="26" viewBox="0 0 24 24" fill="#fff"><path d="M12 2a8 8 0 0 0-5 14v6h8v-3h3v-5l2-1-2-4A8 8 0 0 0 12 2z"/></svg></div>
  <div class="abs benefit" style="left:717px;top:2118px"><h4>Inclusive Mindset</h4><p>We believe great leadership embraces diversity</p></div>

  <div class="abs b-icon" style="left:692px;top:2214px"><svg width="30" height="30" viewBox="0 0 24 24" fill="none" stroke="#fff" stroke-width="1.8"><path d="M2 11l5-4 5 3 5-3 5 4-8 7z"/></svg></div>
  <div class="abs benefit" style="left:769px;top:2207px"><h4>Partnership for Growth</h4><p>We walk alongside our clients, guiding leaders<br>and teams unlock their full potential</p></div>

  <div class="abs b-icon" style="left:747px;top:2300px"><svg width="28" height="28" viewBox="0 0 24 24" fill="none" stroke="#fff" stroke-width="2"><path d="M3 3l6 6M21 3l-6 6M3 21l6-6M21 21l-6-6M9 5v4H5M15 5v4h4M9 19v-4H5M15 19v-4h4"/></svg></div>
  <div class="abs benefit" style="left:823px;top:2318px"><h4>Tailored for Lasting Impact</h4><p>Every program we design is customized<br>to your organization's unique needs</p></div>
</section>

<section>
  <div class="abs testimonials"></div>
  <h2 class="abs section-title" style="left:0;top:2512px;width:1200px">CLIENT TESTIMONIALS</h2>
  <div class="abs eyebrow" style="left:0;top:2576px;width:1200px">REVIEWS</div>

  <div class="abs avatar" style="left:116px;top:2646px" role="img" aria-label="Client headshot"></div>
  <div class="abs t-role" style="left:225px;top:2652px">Senior HR Partner</div>
  <div class="abs stars" style="left:222px;top:2680px">★★★★★</div>
  <p class="abs t-quote" style="left:111px;top:2737px">“The leadership academy designed by BrightPath transformed how our managers approach collaboration and decision-making. The impact was visible within weeks.”</p>

  <div class="abs divider"></div>

  <div class="abs avatar" style="left:648px;top:2646px" role="img" aria-label="Client headshot"></div>
  <div class="abs t-role" style="left:754px;top:2652px">VP of Strategy</div>
  <div class="abs stars" style="left:752px;top:2680px">★★★★★</div>
  <p class="abs t-quote" style="left:643px;top:2737px">“Our strategy workshop was engaging, inclusive, and exactly what we needed to align as a leadership team. BrightPath created a space where every voice was heard.”</p>

  <div class="abs dots"><span></span><span class="on"></span><span></span></div>
</section>

<section>
  <h2 class="abs section-title" style="left:0;top:2998px;width:1200px">LATEST NEWS</h2>
  <div class="abs eyebrow" style="left:0;top:3062px;width:1200px">OUR BLOG</div>

  <article class="abs post" style="left:115px">
    <div class="ph" role="img" aria-label="Presenter at a whiteboard with a seated team" style="background:linear-gradient(160deg,#dfe6ec,#8d939a)"></div>
    <div class="body"><div class="cat">News</div><h3>Why Emotional Intelligence Is the Key to Effective Leadership</h3><div class="meta"><span>▦ Sep 12,,2025</span><span>▭ 4 Comments</span></div></div>
  </article>
  <article class="abs post" style="left:443px">
    <div class="ph" role="img" aria-label="Team gathered in a strategy session" style="background:linear-gradient(160deg,#e0a53a,#5a4e46)"></div>
    <div class="body"><div class="cat">News</div><h3>How to Facilitate Strategy Sessions That Drive Real Action”</h3><div class="meta"><span>▦ Sep 12,,2025</span><span>▭ 4 Comments</span></div></div>
  </article>
  <article class="abs post" style="left:771px">
    <div class="ph" role="img" aria-label="Colleagues discussing around a table" style="background:linear-gradient(160deg,#b6664a,#d9d4cd)"></div>
    <div class="body"><div class="cat">News</div><h3>5 Coaching Questions Every Leader Should Ask Themselves</h3><div class="meta"><span>▦ Sep 12,,2025</span><span>▭ 4 Comments</span></div></div>
  </article>
</section>

<footer>
  <svg class="abs footer-bg" width="1200" height="402" viewBox="0 0 1200 402">
    <path d="M0 105 L600 0 L1200 105 L1200 402 L0 402 Z" fill="#2a7fcf"/>
  </svg>
  <div class="abs f-brand">
    <span class="mark"></span>
    <span class="name">BrightPath</span>
  </div>
  <div class="abs socials"><span></span><span></span><span></span><span></span></div>
  <nav class="abs f-links">
    <span>Home</span><span>|</span><span>About Us</span><span>|</span><span>Services</span><span>|</span><span>Testimonials</span><span>|</span><span>Case Studies</span><span>|</span><span>Contact Us</span>
  </nav>
  <div class="abs f-contact" style="left:193px">
    <svg width="26" height="26" viewBox="0 0 24 24"><circle cx="12" cy="12" r="12" fill="#fff"/><path d="M12 5a4.5 4.5 0 0 0-4.5 4.5C7.5 13 12 19 12 19s4.5-6 4.5-9.5A4.5 4.5 0 0 0 12 5z" fill="#2a7fcf"/><circle cx="12" cy="9.5" r="1.7" fill="#fff"/></svg>
    Lorem Ipsum, lorem -437916
  </div>
  <div class="abs f-contact" style="left:545px;top:3868px">
    <svg width="26" height="26" viewBox="0 0 24 24"><circle cx="12" cy="12" r="12" fill="#fff"/><path d="M8 6l2.5 0 1 3-1.5 1.2a8 8 0 0 0 3.8 3.8L15 12.5l3 1v2.5c0 .8-.7 1.4-1.5 1.3A10 10 0 0 1 6.7 7.5C6.6 6.7 7.2 6 8 6z" fill="#2a7fcf"/></svg>
    +1 888 888 8888
  </div>
  <div class="abs f-contact" style="left:820px;top:3858px">
    <svg width="28" height="28" viewBox="0 0 24 24"><circle cx="12" cy="12" r="12" fill="#fff"/><rect x="6" y="8" width="12" height="9" rx="1" fill="none" stroke="#2a7fcf" stroke-width="1.6"/><path d="M6 8.5l6 4.5 6-4.5" fill="none" stroke="#2a7fcf" stroke-width="1.6"/></svg>
    info@brightpath.com
  </div>
  <div class="abs f-line"></div>
  <div class="abs copyright">© 2025 BrightPath consult . All rights reserved</div>
</footer>

</body>
</html>
```